Flag Order

We were just looking to order some branding flags to put on our rental equipment for our business. We would like different examples of the colors, shapes, sizes, backgrounds etc. Was thinking of just doing the plains icon instead of the whole logo on there. but open to ideas. preferably not a white background as they could get dirty,

```html
<!DOCTYPE html>
<html lang="en">
<head>
<meta charset="utf-8">
<title>Ridgeline Tool Rentals – Banner Flag</title>
<link rel="stylesheet" href="https://fonts.googleapis.com/css2?family=Archivo+Black&family=Oswald:wght@500;600&display=swap">
<style>
  :root {
    --backdrop: #666666;
    --flag-blue: #1c9ee6;
    --flag-black: #2a2a2a;
    --flag-white: #ffffff;
  }
  * { margin: 0; padding: 0; box-sizing: border-box; }
  html, body {
    width: 1200px;
    height: 1200px;
    overflow: hidden;
    background: var(--backdrop);
  }
  .canvas {
    position: relative;
    width: 1200px;
    height: 1200px;
  }
  .banner-flag {
    position: absolute;
    left: 416px;
    top: 80px;
    width: 368px;
    height: 1040px;
  }
  .flag-top {
    position: absolute;
    left: 0; top: 0;
    width: 368px;
    height: 730px;
    background: var(--flag-blue);
  }
  .flag-divider {
    position: absolute;
    left: 162px;
    top: 0;
    width: 3px;
    height: 730px;
    background: var(--flag-white);
  }
  .vertical-text {
    position: absolute;
    writing-mode: vertical-rl;
    transform: rotate(180deg);
    color: var(--flag-white);
    white-space: nowrap;
  }
  .contact-block {
    left: 36px;
    bottom: 40px;
    font-family: "Oswald", sans-serif;
  }
  .contact-phone {
    font-size: 54px;
    font-weight: 600;
    line-height: 1;
    letter-spacing: 0.01em;
  }
  .contact-web {
    font-size: 23px;
    font-weight: 500;
    line-height: 1.3;
    letter-spacing: 0.05em;
    margin-right: 10px;
  }
  .brand-block {
    left: 196px;
    bottom: 40px;
    font-family: "Archivo Black", sans-serif;
  }
  .brand-name {
    font-size: 62px;
    line-height: 1;
  }
  .brand-tagline {
    font-size: 19px;
    line-height: 1;
    letter-spacing: 0.9em;
    margin-right: 20px;
  }
  .flag-bottom {
    position: absolute;
    left: 0;
    top: 730px;
    width: 368px;
    height: 310px;
    background: var(--flag-black);
    display: flex;
    align-items: center;
    justify-content: center;
  }
  .brand-mark-name {
    font-family: "Archivo Black", sans-serif;
    font-size: 42px;
    line-height: 1;
    color: var(--flag-white);
  }
</style>
</head>
<body>
  <main class="canvas">
    <section class="banner-flag">
      <div class="flag-top">
        <div class="flag-divider"></div>
        <div class="vertical-text contact-block">
          <div class="contact-phone">555-014-2290</div>
          <div class="contact-web">RIDGELINETOOLRENTALS.COM</div>
        </div>
        <div class="vertical-text brand-block">
          <div class="brand-name">RIDGELINE</div>
          <div class="brand-tagline">TOOL RENTALS</div>
        </div>
      </div>
      <div class="flag-bottom">
        <span class="brand-mark-name">RIDGELINE</span>
      </div>
    </section>
  </main>
</body>
</html>
```